Roofing company in Toronto, Canada needs a logo design and business card design

We need a business card and logo created for our company. Our company is "KLV Roofing" which provides roofing services for commercial and residential customers. We serve customers in the Greater Toronto Area (in Canada) thus the name KLV.

We want the logo and business card to be a modern design displaying professionalism and quality in the work. We would prefer rounded corners for the business cards but are open to other ideas. The cards should be pleasant and appealing to customers.

Target Market(s)

Commercial and Residential customers

Industry/Entity Type

Roofing

Contact Information for Business Card

Logo Text

KLV Roofing

Requirements
Nice to have
• Colours that are pleasing to the eye but at the same time should stand out from other business cards. If the design can incorporate the name of KLV Roofing and the actual concept of roofing that would be nice.
Should not have
• Do not want the business cards or logo to be childish looking. Need to look professionally designed.

```html
<!DOCTYPE html>
<html lang="en">
<head>
<meta charset="utf-8">
<title>KLV Roofing – Business Card</title>
<link href="https://fonts.googleapis.com/css2?family=Source+Sans+3:wght@400;600;700&display=swap" rel="stylesheet">
<style>
  :root {
    --stage: #000000;
    --card-light: #f3f3f3;
    --brand-red: #b30000;
    --brand-red-deep: #a30000;
    --text-grey: #3c3c3c;
    --white: #ffffff;
  }
  html, body {
    margin: 0;
    padding: 0;
    width: 1200px;
    height: 900px;
    overflow: hidden;
    background: var(--stage);
    font-family: "Source Sans 3", "Myriad Pro", Arial, sans-serif;
  }
  .canvas {
    position: relative;
    width: 1200px;
    height: 900px;
    background: var(--stage);
  }
  .card {
    position: absolute;
    top: 200px;
    width: 310px;
    height: 502px;
    box-sizing: border-box;
    overflow: hidden;
  }
  .card--front {
    left: 265px;
    background: var(--card-light);
    border-radius: 46px 0 46px 0;
  }
  .card--back {
    left: 641px;
    width: 309px;
    background: var(--brand-red);
    border-radius: 0 46px 0 46px;
  }
  .back-decoration {
    position: absolute;
    left: 0;
    top: 14px;
    width: 309px;
    height: 336px;
    background: linear-gradient(160deg, rgba(120,0,0,0) 0%, rgba(120,0,0,0.22) 45%, rgba(120,0,0,0.12) 80%, rgba(120,0,0,0) 100%);
  }

  .wordmark {
    position: absolute;
    font-weight: 700;
    line-height: 1;
    text-align: center;
  }
  .wordmark__top {
    display: flex;
    align-items: center;
    justify-content: center;
    gap: 10px;
  }
  .wordmark__name { display: block; letter-spacing: 0.06em; }
  .wordmark__sub { display: block; }
  .wordmark__square { flex: none; }

  .card--front .wordmark {
    left: 33px;
    width: 244px;
    top: 48px;
    color: var(--brand-red);
  }
  .card--front .wordmark__name { font-size: 70px; }
  .card--front .wordmark__square { width: 14px; height: 14px; background: var(--brand-red); margin-top: 22px; }
  .card--front .wordmark__sub { font-size: 36px; letter-spacing: 0.29em; margin: 4px 0 0 0.29em; }

  .card--back .wordmark {
    left: 50px;
    width: 204px;
    top: 360px;
    color: var(--white);
  }
  .card--back .wordmark__name { font-size: 58px; }
  .card--back .wordmark__square { width: 12px; height: 12px; background: var(--white); margin-top: 18px; }
  .card--back .wordmark__sub { font-size: 31px; letter-spacing: 0.26em; margin: 4px 0 0 0.26em; }

  .contact {
    position: absolute;
    left: 27px;
    top: 327px;
    color: var(--text-grey);
    font-size: 14.5px;
    line-height: 16px;
  }
  .contact__name {
    margin: 0;
    color: var(--brand-red);
    font-size: 18.5px;
    font-weight: 600;
    line-height: 22px;
  }
  .contact__role { margin: 2px 0 19px; }
  .contact__address { margin: 0 0 12px; font-style: normal; }
  .contact__line {
    display: flex;
    align-items: center;
    gap: 7px;
    margin: 0 0 3px;
  }
  .contact__icon { width: 10px; height: 10px; flex: none; }
</style>
</head>
<body>
<main class="canvas">
  <section class="card card--front">
    <div class="wordmark">
      <div class="wordmark__top">
        <span class="wordmark__name">KLV</span>
        <span class="wordmark__square" aria-hidden="true"></span>
      </div>
      <span class="wordmark__sub">ROOFING</span>
    </div>
    <div class="contact">
      <p class="contact__name">JOHN SMITH</p>
      <p class="contact__role">Managing Director</p>
      <address class="contact__address">1234, Address Goes Here<br>Country Name, 123456</address>
      <p class="contact__line">
        <svg class="contact__icon" viewBox="0 0 10 10" aria-hidden="true">
          <path d="M1 4 Q5 0 9 4 L8 5 L6.5 4 L6.5 3 Q5 2.5 3.5 3 L3.5 4 L2 5 Z M2.5 5.5 L7.5 5.5 L8.5 9 L1.5 9 Z" fill="#b30000"/>
        </svg>
        823-456-7890
      </p>
      <p class="contact__line">
        <svg class="contact__icon" viewBox="0 0 10 10" aria-hidden="true">
          <rect x="0.5" y="2" width="9" height="6.5" fill="#b30000"/>
          <path d="M0.8 2.4 L5 5.6 L9.2 2.4" fill="none" stroke="#f3f3f3" stroke-width="0.9"/>
        </svg>
        info@youremail.com
      </p>
    </div>
  </section>

  <section class="card card--back">
    <div class="back-decoration" role="img" aria-label="Faint tone-on-tone roof decoration"></div>
    <div class="wordmark">
      <div class="wordmark__top">
        <span class="wordmark__name">KLV</span>
        <span class="wordmark__square" aria-hidden="true"></span>
      </div>
      <span class="wordmark__sub">ROOFING</span>
    </div>
  </section>
</main>
</body>
</html>
```